Detail Shop Business card design

i need a business card design for my new detailing company called 'Brisk's Polish Works'. i want an all black and white design . simple, direct and to the point. i want the designer to choose a fitting font to match the logothe front should have logo, address, phone and email and the back side should have a slogan and text indicating that we offer services on anything including cars, trucks, motorcycles and RVs. slogan will read "we take pride in your ride"
maybe also very small on the back side the IG icon with Brisks_Polish_Works

phone 208.417.6352
address 3847 E Larkin Ave
Spokane WA 99214
email: BrisksPolish@mailvexo.com

Target Market(s)

all ages , auto enthusiasts

Industry/Entity Type

Automotive

Contact Information for Business Card

the front should have logo, address, phone and email and the back side should have a slogan and text indicating that we offer services on anything including cars, trucks, motorcycles and RVs. slogan will read "we take pride in your ride"

phone 208.417.6352
address 3847 E Larkin Ave
Spokane WA 99214

Colors
000000
ffffff

Requirements
Must have
• bold font and very simple design with good spacing
Nice to have
• anything creative from the designer indicating we service any types of vehicles
Should not have
• any colors ,

```html
<!DOCTYPE html>
<html lang="en">
<head>
<meta charset="utf-8">
<title>Brisk's Polish Works — Business Card</title>
<link rel="stylesheet" href="https://fonts.googleapis.com/css2?family=Lato:wght@400;900&family=Tinos&family=Great+Vibes&display=swap">
<style>
  :root {
    --ink: #000000;
    --paper: #ffffff;
    --backdrop: #8c8c8c;
    --rule-light: #9a9a9a;
  }
  * { margin: 0; padding: 0; box-sizing: border-box; }
  html, body { width: 1200px; height: 1200px; overflow: hidden; }
  body { background: var(--backdrop); position: relative; font-family: "Lato", sans-serif; }

  .card { position: absolute; top: 310px; height: 594px; }
  .card--front { left: 234px; width: 364px; background: var(--paper); color: var(--ink); }
  .card--back { left: 627px; width: 369px; background: var(--ink); color: var(--paper); }

  .brand {
    position: absolute; left: 0; right: 0; top: 150px;
    display: flex; flex-direction: column; align-items: center; gap: 14px;
  }
  .brand__dot { width: 22px; height: 22px; border-radius: 50%; background: currentColor; }
  .brand__name {
    font-family: "Lato", sans-serif; font-weight: 900; font-size: 30px;
    text-transform: uppercase; letter-spacing: 1px; line-height: 1.15; text-align: center;
  }

  .contact { position: absolute; left: 0; right: 0; text-align: center; font-size: 16px; line-height: 22px; }
  .contact--reach { top: 375px; }
  .contact--address { top: 445px; }
  .contact--social { top: 523px; }
  .rule { position: absolute; left: 87px; width: 190px; height: 1px; background: var(--ink); }
  .rule--one { top: 431px; }
  .social-divider { position: absolute; left: 87px; width: 190px; top: 499px; height: 16px; }
  .social-divider::before, .social-divider::after {
    content: ""; position: absolute; top: 8px; width: 82px; height: 1px; background: var(--ink);
  }
  .social-divider::before { left: 0; }
  .social-divider::after { right: 0; }
  .social-divider__dot {
    position: absolute; left: 87px; top: 0; width: 16px; height: 16px; border-radius: 50%; background: var(--ink);
  }

  .services {
    position: absolute; left: 0; right: 0; top: 355px;
    font-family: "Tinos", serif; font-size: 22px; line-height: 40px;
    text-align: center; text-transform: uppercase; letter-spacing: 0.3px;
  }
  .rule--back { left: 39px; width: 285px; top: 486px; background: var(--rule-light); }
  .slogan {
    position: absolute; left: 0; right: 0; top: 508px; text-align: center;
    font-family: "Great Vibes", cursive; font-size: 40px; white-space: nowrap;
  }
</style>
</head>
<body>
  <section class="card card--front" aria-label="Card front">
    <div class="brand">
      <span class="brand__dot"></span>
      <span class="brand__name">Brisk's<br>Polish Works</span>
    </div>
    <p class="contact contact--reach">208.417.6352<br>BrisksPolish@mailvexo.com</p>
    <div class="rule rule--one"></div>
    <p class="contact contact--address">3847 E Larkin Ave<br>Spokane WA 99214</p>
    <div class="social-divider"><span class="social-divider__dot"></span></div>
    <p class="contact contact--social">Brisks_Polish_Works</p>
  </section>

  <section class="card card--back" aria-label="Card back">
    <div class="brand">
      <span class="brand__dot"></span>
      <span class="brand__name">Brisk's<br>Polish Works</span>
    </div>
    <p class="services">We offer services on<br>including&nbsp; cars, trucks<br>motorcycles and RVs.</p>
    <div class="rule rule--back"></div>
    <p class="slogan">We take pride in your ride</p>
  </section>
</body>
</html>
```